Dynamic Business Card for Sports Supplements Company

Hi! I'm looking for an awesome business card to match my existing sports supplement company. I have uploaded my current company logo and screenshot of the front page of my website.

I would like to have something dynamic and interesting and utilize the colors in the website - the reds and purples

The business card should be double sided and focus on a unique eye-catching design on the back and include all the relevant company info.

Most importantly, it should say somewhere: "Sign up on our website for a coupon code."

Target Market(s)

Mostly for women gym goers but it shouldn't be too feminine. It should be in keeping with the website design. It should flow and clearly be connected to it

Industry/Entity Type

Business

Contact Information for Business Card

Lorraine K. Vestal
CEO
LVestal@Quorvanexco.com
www.quorvanexco.com
555.417.3820
P.O. Box 47315
Carrow Glen, Westmere 00000

Sign up on our website for a coupon code

Font styles to use
Serif
Sans Serif
Other font styles liked:
• Novecento font family and "Quorvanex" is in AR Destine font

Requirements
Must have
• One side should be a bold Quorvanex logo design. Even just the symbol itself may be o.k. (see attached file)

```html
<!DOCTYPE html>
<html lang="en">
<head>
<meta charset="utf-8">
<title>Quorvanex Business Card</title>
<link href="https://fonts.googleapis.com/css2?family=Source+Sans+3:ital,wght@0,400;0,600;0,700;1,400&family=Michroma&display=swap" rel="stylesheet">
<style>
  :root {
    --backdrop: #4b4036;
    --card-black: #000000;
    --brand-red: #ed1c24;
    --pattern-red: #ee2a32;
    --white: #ffffff;
    --muted: #d9d9d9;
  }
  * { margin: 0; padding: 0; box-sizing: border-box; }
  html, body {
    width: 1200px; height: 987px; overflow: hidden;
    background: var(--backdrop);
    font-family: "Source Sans 3", "Myriad Pro", sans-serif;
  }
  .canvas { position: relative; width: 1200px; height: 987px; }
  .card {
    position: absolute; left: 293px; width: 614px; height: 351px;
    box-shadow: 0 3px 8px rgba(0,0,0,0.45);
    overflow: hidden;
  }
  .card--front { top: 130px; background: var(--card-black); }
  .card--back { top: 506px; background: var(--brand-red); }

  .brand-mark {
    position: absolute; left: 110px; top: 38px;
    width: 56px; height: 56px; background: var(--brand-red);
  }
  .brand-name {
    position: absolute; left: 41px; top: 122px;
    font-weight: 700; font-size: 34px; letter-spacing: 1px;
    color: var(--white); text-transform: uppercase; line-height: 1;
  }
  .tagline {
    font-family: "Michroma", sans-serif;
    font-size: 8.5px; letter-spacing: 1.6px; color: var(--muted);
    text-transform: uppercase; line-height: 1;
  }
  .card--front .tagline { position: absolute; left: 41px; top: 156px; }

  .address {
    position: absolute; left: 41px; top: 201px;
    color: var(--white); font-size: 15.5px; line-height: 22px; font-style: normal;
  }
  .contact-list {
    position: absolute; left: 41px; top: 251px; list-style: none;
    color: var(--white); font-size: 15.5px;
  }
  .contact-list li { display: flex; align-items: center; height: 23.5px; }
  .contact-list svg { width: 14px; height: 14px; margin-right: 8px; flex: none; }

  .name-band {
    position: absolute; left: 340px; top: 222px; width: 274px; height: 77px;
  }
  .name-band svg { position: absolute; inset: 0; }
  .name-band__text {
    position: absolute; right: 18px; top: 10px; text-align: right; color: var(--white);
  }
  .person-name { font-size: 22px; font-weight: 600; line-height: 28px; }
  .person-role { font-size: 16px; line-height: 22px; }

  .pattern-field {
    position: absolute; inset: 0;
    background: linear-gradient(180deg, var(--pattern-red), var(--brand-red));
  }
  .back-lockup {
    position: absolute; left: 0; right: 0; top: 142px; text-align: center; color: var(--white);
  }
  .back-lockup .brand-name-back {
    font-weight: 700; font-size: 42px; letter-spacing: 1.5px;
    text-transform: uppercase; line-height: 1;
  }
  .back-lockup .tagline { margin-top: 5px; color: var(--white); font-size: 10px; letter-spacing: 2px; }
  .coupon-note { margin-top: 6px; font-style: italic; font-size: 16.5px; }
</style>
</head>
<body>
<main class="canvas">
  <section class="card card--front" aria-label="Card front">
    <div class="brand-mark"></div>
    <div class="brand-name">Quorvanex</div>
    <div class="tagline">Your Strength Companion</div>

    <address class="address">
      P.O. Box 47315<br>Carrow Glen, Westmere 00000
    </address>
    <ul class="contact-list">
      <li>
        <svg viewBox="0 0 24 24"><path fill="#ed1c24" d="M6.6 10.8a15.1 15.1 0 0 0 6.6 6.6l2.2-2.2c.3-.3.7-.4 1-.2 1.1.4 2.3.6 3.6.6.6 0 1 .4 1 1V20c0 .6-.4 1-1 1A17 17 0 0 1 3 4c0-.6.4-1 1-1h3.5c.6 0 1 .4 1 1 0 1.3.2 2.5.6 3.6.1.3 0 .7-.2 1z"/></svg>
        555.417.3820
      </li>
      <li>
        <svg viewBox="0 0 24 24"><rect x="2" y="5" width="20" height="14" fill="#ed1c24"/><path d="M2 5l10 8 10-8" fill="none" stroke="#000" stroke-width="1.6"/></svg>
        LVestal@Quorvanexco.com
      </li>
      <li>
        <svg viewBox="0 0 24 24"><circle cx="12" cy="12" r="10" fill="#ed1c24"/><path d="M2 12h20M12 2c3 3 3 17 0 20M12 2c-3 3-3 17 0 20" fill="none" stroke="#000" stroke-width="1.4"/></svg>
        www.quorvanexco.com
      </li>
    </ul>

    <div class="name-band">
      <svg viewBox="0 0 274 77" aria-hidden="true">
        <polygon fill="#ed1c24" points="16,0 26,0 10,38.5 26,77 16,77 0,38.5"/>
        <polygon fill="#ffffff" points="32,0 46,0 30,38.5 46,77 32,77 16,38.5"/>
        <polygon fill="#ed1c24" points="54,0 274,0 274,77 54,77 38,38.5"/>
      </svg>
      <div class="name-band__text">
        <div class="person-name">Lorraine K. Vestal</div>
        <div class="person-role">CEO</div>
      </div>
    </div>
  </section>

  <section class="card card--back" aria-label="Card back">
    <div class="pattern-field" role="img" aria-label="Repeating red chevron pattern background"></div>
    <div class="back-lockup">
      <div class="brand-name-back">Quorvanex</div>
      <div class="tagline">Your Strength Companion</div>
      <div class="coupon-note">Sign up on our website for a coupon code</div>
    </div>
  </section>
</main>
</body>
</html>
```